Design NEW business card

We would like a business card using the colour deep red wine or dark navy blue textured background (patterned or not, open to suggestions) with a high gloss debossed rose gold/copper RM Roland Mercer Jewellery business name (Provided). I have included images for your review we would like to keep our currently logo and business name on the front but you can change the layout and positioning. For the back of the card we are open to all suggestions/variations.
Business
Use our current RM Roland Mercer Jewellery logo (Provided image)

```html
<!DOCTYPE html>
<html lang="en">
<head>
<meta charset="utf-8">
<title>Roland Mercer Jewellery — Business Card</title>
<link rel="stylesheet" href="https://fonts.googleapis.com/css2?family=Open+Sans:wght@400;500&display=swap">
<style>
  :root {
    --backdrop: #000000;
    --card-front: #35363a;
    --card-back: #5e2529;
    --rose-gold: #c99277;
    --text-light: #f4f4f4;
    --divider: #55565b;
  }
  * { margin: 0; padding: 0; box-sizing: border-box; }
  html, body {
    width: 1200px; height: 900px; overflow: hidden;
    background: var(--backdrop);
    font-family: "Open Sans", Arial, sans-serif;
  }
  .canvas { position: relative; width: 1200px; height: 900px; }
  .card {
    position: absolute; top: 271px;
    width: 457px; height: 281px;
    border-radius: 14px; overflow: hidden;
  }
  .card-front { left: 137px; background: var(--card-front); }
  .card-back {
    left: 626px;
    background: radial-gradient(ellipse at 50% 45%, #66292e 0%, var(--card-back) 70%, #552024 100%);
  }
  .brand-name {
    position: absolute;
    color: var(--rose-gold);
    font-weight: 400;
    letter-spacing: 0.12em;
    text-transform: uppercase;
    white-space: nowrap;
    display: flex; align-items: center; gap: 8px;
  }
  .brand-mark {
    width: 8px; height: 8px; border-radius: 50%;
    background: var(--rose-gold);
    flex: none;
  }
  .brand-lines { display: flex; flex-direction: column; align-items: center; }
  .card-front .brand-name {
    left: 46px; top: 128px; width: 178px;
    justify-content: center;
    font-size: 12px; line-height: 17px;
  }
  .card-back .brand-name {
    left: 50%; top: 50%; transform: translate(-50%, -50%);
    font-size: 19px; line-height: 26px; gap: 12px;
  }
  .card-back .brand-mark { width: 11px; height: 11px; }
  .divider {
    position: absolute; left: 234px; top: 72px;
    width: 1px; height: 140px; background: var(--divider);
  }
  .details {
    position: absolute; left: 246px; top: 71px;
    color: var(--text-light);
  }
  .person-name { font-size: 18px; font-weight: 400; line-height: 22px; }
  .person-title { font-size: 12px; line-height: 16px; margin-top: 1px; }
  .address { font-size: 12px; line-height: 16px; margin-top: 11px; }
  .contact-list { list-style: none; margin-top: 11px; font-size: 12px; line-height: 16.5px; }
  .contact-list li { display: flex; align-items: center; gap: 7px; }
  .contact-list svg { width: 10px; height: 10px; fill: var(--text-light); flex: none; }
</style>
</head>
<body>
<main class="canvas">
  <section class="card card-front">
    <div class="brand-name">
      <span class="brand-mark"></span>
      <span class="brand-lines"><span>Roland Mercer</span><span>Jewellery</span></span>
    </div>
    <div class="divider"></div>
    <div class="details">
      <h1 class="person-name">Adrian Vale</h1>
      <p class="person-title">Managing Director</p>
      <p class="address">12345, Address Goes Here<br>Country Name, 123456.</p>
      <ul class="contact-list">
        <li><svg viewBox="0 0 10 10" aria-hidden="true"><path d="M2 0.5 L3.6 2.6 L2.8 3.6 C3.4 5 4.9 6.6 6.4 7.2 L7.4 6.4 L9.5 8 L8.4 9.5 C4.5 9 1 5.5 0.5 1.6 Z"/></svg>044-987 654 321</li>
        <li><svg viewBox="0 0 10 10" aria-hidden="true"><path d="M0.5 2 H9.5 V8.5 H0.5 Z M1.2 2.6 L5 5.6 L8.8 2.6" stroke="#35363a" stroke-width="0.8"/></svg>info@rolandmercer.com</li>
        <li><svg viewBox="0 0 10 10" aria-hidden="true"><path d="M4 6 L6 4 M3.4 4.6 L1.8 6.2 A1.5 1.5 0 0 0 3.8 8.2 L5.4 6.6 M6.6 5.4 L8.2 3.8 A1.5 1.5 0 0 0 6.2 1.8 L4.6 3.4" fill="none" stroke="#f4f4f4" stroke-width="1.1" stroke-linecap="round"/></svg>www.rolandmercer.com</li>
      </ul>
    </div>
  </section>
  <section class="card card-back">
    <div class="brand-name">
      <span class="brand-mark"></span>
      <span class="brand-lines"><span>Roland Mercer</span><span>Jewellery</span></span>
    </div>
  </section>
</main>
</body>
</html>
```